RW Framewell Inc Business cards

We need business cards using our existing logo but slightly modified. Right now the logo says RW Loadbearing Masonry. We want to keep the RW part of the design, but replace the Structural Concrete portion with "FRAMEWELL". Please see the attached file.
Ideally this would be a blank template so we can add Different Names, titles, and phone numbers later.
On the one side we want only the logo and on the other side the detail. I'm attaching an example for you to see.
Please reach out with any other questions. Our address and other details will be given out once we find a design we like.

Target Market(s)

Construction Industry

```html
<!DOCTYPE html>
<html lang="en">
<head>
<meta charset="utf-8">
<title>RW Framewell Inc – Business Cards</title>
<link rel="stylesheet" href="https://fonts.googleapis.com/css2?family=Arimo:wght@400;700&display=swap">
<style>
  :root {
    --backdrop: #2b2f36;
    --brand-blue: #1177c0;
    --card-white: #ffffff;
    --text-dark: #2a2a2a;
  }
  * { box-sizing: border-box; margin: 0; padding: 0; }
  html, body {
    width: 1200px;
    height: 1000px;
    overflow: hidden;
    background: var(--backdrop);
    font-family: "Arimo", Arial, sans-serif;
  }
  .canvas {
    width: 1200px;
    height: 1000px;
    display: flex;
    flex-direction: column;
    align-items: center;
    justify-content: center;
    gap: 40px;
  }
  .card {
    width: 760px;
    height: 434px;
    border-radius: 22px;
    position: relative;
    box-shadow: 0 14px 30px rgba(0, 0, 0, 0.45);
  }
  .card--front {
    background: var(--brand-blue);
    display: flex;
    align-items: center;
    justify-content: center;
  }
  .card--back { background: var(--card-white); }

  .wordmark {
    display: flex;
    flex-direction: column;
    align-items: flex-start;
    font-weight: 700;
    line-height: 1;
    white-space: nowrap;
  }
  .wordmark__initials { letter-spacing: 0.02em; }
  .wordmark__word { letter-spacing: 0.55em; }

  .card--front .wordmark { color: var(--card-white); }
  .card--front .wordmark__initials { font-size: 150px; }
  .card--front .wordmark__word { font-size: 34px; margin-top: 6px; }

  .card--back .wordmark {
    position: absolute;
    top: 36px;
    left: 60px;
    color: var(--brand-blue);
  }
  .card--back .wordmark__initials { font-size: 104px; }
  .card--back .wordmark__word { font-size: 24px; margin-top: 4px; }

  .person {
    position: absolute;
    left: 60px;
    top: 228px;
  }
  .person__name {
    color: var(--brand-blue);
    font-weight: 700;
    font-size: 32px;
    letter-spacing: 0.01em;
  }
  .person__title {
    color: var(--text-dark);
    font-size: 20px;
    margin-top: 2px;
  }
  .contact {
    position: absolute;
    right: 60px;
    bottom: 36px;
    color: var(--text-dark);
    font-size: 20px;
    line-height: 1.3;
  }
  .contact__address { padding-left: 30px; }
  .contact__row {
    display: flex;
    align-items: center;
    gap: 10px;
  }
  .contact__icon {
    width: 19px;
    height: 19px;
    flex: none;
    fill: var(--brand-blue);
  }
</style>
</head>
<body>
  <main class="canvas">
    <section class="card card--front" aria-label="Card front">
      <div class="wordmark">
        <span class="wordmark__initials">RW</span>
        <span class="wordmark__word">FRAMEWELL</span>
      </div>
    </section>

    <section class="card card--back" aria-label="Card back">
      <div class="wordmark">
        <span class="wordmark__initials">RW</span>
        <span class="wordmark__word">FRAMEWELL</span>
      </div>

      <div class="person">
        <p class="person__name">DALEN WHITCOMBE</p>
        <p class="person__title">Owner/CEO</p>
      </div>

      <div class="contact">
        <p class="contact__address">418 Ridgeline Avenue<br>County Name 7604</p>
        <p class="contact__row">
          <svg class="contact__icon" viewBox="0 0 24 24" aria-hidden="true"><path d="M6.6 10.8a15.1 15.1 0 0 0 6.6 6.6l2.2-2.2a1 1 0 0 1 1-.25 11.4 11.4 0 0 0 3.6.57 1 1 0 0 1 1 1V20a1 1 0 0 1-1 1A17 17 0 0 1 3 4a1 1 0 0 1 1-1h3.5a1 1 0 0 1 1 1c0 1.25.2 2.45.57 3.57a1 1 0 0 1-.25 1z"/></svg>
          <span>555-014-7730</span>
        </p>
        <p class="contact__row">
          <svg class="contact__icon" viewBox="0 0 24 24" aria-hidden="true"><path d="M2 5h20v14H2z M4 7v.4l8 5.2 8-5.2V7z" fill-rule="evenodd"/></svg>
          <span>info@rwframewell.com</span>
        </p>
        <p class="contact__row">
          <svg class="contact__icon" viewBox="0 0 24 24" aria-hidden="true"><circle cx="12" cy="12" r="10"/><path d="M2 12h20M12 2c3 3 3 17 0 20M12 2c-3 3-3 17 0 20" stroke="#fff" stroke-width="1.4" fill="none"/></svg>
          <span>www.rwframewell.com</span>
        </p>
      </div>
    </section>
  </main>
</body>
</html>
```